The design should look similar to the uploaded example to accommodate the information needed for a business card template. I would like to see the colors orange and charcoal grey incorporated along with the logo.The following should be on the back of the card SPECIALIZING IN NEW AND USED TIRES & WHEELS FOR:- Loaders- Skid Steers- Telehandlers- Boom Lifts- Forklifs and moreELIMINATING DOWNTIMEWheel Exchange Program for New & Used Foam Filled and Solid Rubber TiresSPECIALTY SERVICES- Foam Filling Tires- Largest Tire Press in SE- ONSITE Forklift Tire Press- Boom Truck Services - Rubber Tracks

Target Market(s)

New and Existing Customers

Industry/Entity Type

Business

Contact Information for Business Card

NAMEHEAVY DUTY TIRE, LLC8470 Belvedere RoadWest Palm Beach, FL 33411P: 844-HD-TIRESF: 561-431-6469C:E: W: WWW.GRANITERIMSUPPLY-EXAMPLE.COM

Font styles to use
Sans Serif

Colors
f37122
333333

Requirements
Must have
• The logo and the information indicated for the backside of the card
Nice to have
• Keep the orange and charcoal grey colors

```html
<!DOCTYPE html>
<html lang="en">
<head>
<meta charset="utf-8">
<title>Granite Rim Supply — Business Card</title>
<link rel="stylesheet" href="https://fonts.googleapis.com/css2?family=Arvo:wght@700&family=Open+Sans:ital,wght@0,400;0,700;1,400&display=swap">
<style>
  :root {
    --bg: #8f8f8f;
    --paper: #f4f4f2;
    --charcoal: #333333;
    --slate: #2f3b3f;
    --slate-deep: #263034;
    --slate-soft: #3a474b;
    --orange: #f37122;
    --ink: #3c4448;
    --white: #ffffff;
  }
  * { box-sizing: border-box; margin: 0; padding: 0; }
  html, body { width: 1105px; height: 1200px; overflow: hidden; }
  body { background: var(--bg); font-family: "Open Sans", sans-serif; position: relative; }

  .card { position: absolute; left: 182px; width: 746px; height: 425px; overflow: hidden; }
  .card-front { top: 120px; background: var(--paper); }
  .card-back { top: 637px; background: var(--slate); }

  .accent-bar { position: absolute; left: 0; top: 91px; width: 9px; height: 54px; background: var(--orange); }
  .identity { position: absolute; left: 49px; top: 88px; }
  .person-name { font-family: "Arvo", serif; font-weight: 700; font-size: 25px; color: var(--slate); letter-spacing: 0.5px; line-height: 1.1; }
  .person-title { font-family: "Arvo", serif; font-weight: 700; font-size: 18px; color: var(--orange); line-height: 1.3; }

  .address { position: absolute; left: 49px; top: 159px; font-size: 18px; line-height: 27px; color: var(--ink); font-style: normal; }
  .contact-list { position: absolute; left: 49px; top: 220px; list-style: none; font-size: 18px; color: var(--ink); }
  .contact-list li { display: flex; align-items: center; height: 28px; }
  .contact-list svg { width: 18px; height: 18px; margin-right: 12px; fill: var(--slate); flex: none; }

  .brand { position: absolute; left: 408px; top: 268px; display: flex; align-items: center; }
  .brand-dot { width: 66px; height: 66px; border-radius: 50%; background: var(--orange); margin-right: 16px; flex: none; }
  .brand-name { font-family: "Arvo", serif; font-weight: 700; font-size: 22px; line-height: 28px; color: var(--slate); text-align: center; }

  .back-graphic {
    position: absolute; left: -100px; top: -10px; width: 450px; height: 450px; border-radius: 50%;
    background: radial-gradient(circle at 45% 50%, var(--slate-soft) 0%, var(--slate-deep) 100%);
  }

  .services { position: absolute; right: 34px; top: 38px; text-align: right; color: var(--white); }
  .services h2 { font-size: 19.5px; font-weight: 700; line-height: 27px; }
  .services p, .services li { font-size: 18.5px; line-height: 27px; }
  .services ul { list-style: none; }
  .services .item-line { font-style: italic; }
  .bullet { display: inline-block; width: 8px; height: 8px; border-radius: 50%; background: var(--orange); margin: 0 8px; vertical-align: middle; }
  .services section + section { margin-top: 16px; }
</style>
</head>
<body>

<article class="card card-front">
  <div class="accent-bar"></div>
  <div class="identity">
    <div class="person-name">DANA WHITFIELD</div>
    <div class="person-title">CEO/FOUNDER</div>
  </div>
  <address class="address">5126 Marston Lane<br>West Palm Beach, FL 33411</address>
  <ul class="contact-list">
    <li><svg viewBox="0 0 24 24"><path d="M6.6 10.8a15.1 15.1 0 0 0 6.6 6.6l2.2-2.2a1 1 0 0 1 1-.25 11.4 11.4 0 0 0 3.6.57 1 1 0 0 1 1 1V20a1 1 0 0 1-1 1A17 17 0 0 1 3 4a1 1 0 0 1 1-1h3.5a1 1 0 0 1 1 1c0 1.25.2 2.45.57 3.6a1 1 0 0 1-.25 1z"/></svg>&nbsp;844-GR-WHEEL</li>
    <li><svg viewBox="0 0 24 24"><path d="M7 1h10a2 2 0 0 1 2 2v18a2 2 0 0 1-2 2H7a2 2 0 0 1-2-2V3a2 2 0 0 1 2-2zm0 3v14h10V4zm5 15.2a1.2 1.2 0 1 0 0 2.4 1.2 1.2 0 0 0 0-2.4z"/></svg>836 511 2047</li>
    <li><svg viewBox="0 0 24 24"><path d="M6 2h12v5H6zM3 8h18a2 2 0 0 1 2 2v7h-4v5H5v-5H1v-7a2 2 0 0 1 2-2zm4 8v4h10v-4z"/></svg>561-278-9053</li>
    <li><svg viewBox="0 0 24 24"><path d="M2 5h20v14H2zm2 2v.5l8 5 8-5V7l-8 5z"/></svg>dana@graniterimsupply-example.com</li>
    <li><svg viewBox="0 0 24 24"><path d="M12 2a10 10 0 1 0 0 20 10 10 0 0 0 0-20zm-1 17.9A8 8 0 0 1 4.2 10.3L9 15v1a2 2 0 0 0 2 2zm6.9-2.5A2 2 0 0 0 16 16h-1v-3a1 1 0 0 0-1-1H8v-2h2a1 1 0 0 0 1-1V7h2a2 2 0 0 0 2-2v-.4a8 8 0 0 1 2.9 12.8z"/></svg>www.graniterimsupply-example.com</li>
  </ul>
  <div class="brand">
    <div class="brand-dot"></div>
    <div class="brand-name">GRANITE RIM<br>SUPPLY, LLC</div>
  </div>
</article>

<article class="card card-back">
  <div class="back-graphic" role="img" aria-label="Large brand graphic area"></div>
  <div class="services">
    <section>
      <h2>SPECIALIZING IN NEW AND<br>USED TIRES &amp; WHEELS FOR</h2>
      <ul>
        <li class="item-line">Loaders<span class="bullet"></span>Skid Steers<span class="bullet"></span>Telehandlers<span class="bullet"></span></li>
        <li class="item-line">Boom Lifts<span class="bullet"></span>Forklifs and more<span class="bullet"></span></li>
      </ul>
    </section>
    <section>
      <h2>ELIMINATING DOWNTIME</h2>
      <p>Wheel Exchange Program for New &amp;<br>Used Foam Filled and Solid Rubber Tires</p>
    </section>
    <section>
      <h2>SPECIALTY SERVICES</h2>
      <ul>
        <li class="item-line">Foam Filling Tires<span class="bullet"></span></li>
        <li class="item-line">Largest Tire Press in SE<span class="bullet"></span></li>
        <li class="item-line">ONSITE Forklift Tire Press<span class="bullet"></span></li>
        <li class="item-line">Boom Truck Services<span class="bullet"></span>Rubber Tracks<span class="bullet"></span></li>
      </ul>
    </section>
  </div>
</article>

</body>
</html>
```